New Innovative Counselling and psychotherapy Service needs Business Card design

Keep it simple and professional. On one side, just company name and logo (perhaps in all blue) and maybe a tag line.

On other side (all white) my name and Qualifications in centre

Industry/Entity Type

Health And Wellness

Contact Information for Business Card

Dara Whelby
Counsellor & Psychotherapist
BSc (Psychol.), BA, Dip. (Couns. & Psych.), PG.Cert (CBT), FGTrK, ONRE

I will also require Mobile no, Email and web site address of which I'll pass on to final designer.

Font styles to use
Sans Serif

Requirements
Must have
• My Logo Only and please use the colours in logo that is in it.
Should not have
• Any other images

```html
<!DOCTYPE html>
<html lang="en">
<head>
<meta charset="utf-8">
<title>Thrive Lane – Business Card</title>
<link href="https://fonts.googleapis.com/css2?family=Montserrat:wght@400;500;800&display=swap" rel="stylesheet">
<style>
  :root {
    --sky: #4fb3e6;
    --sky-deep: #3aa3dc;
    --steel: #4a90bf;
    --leaf: #8cc152;
    --ink: #3a3a3a;
    --grey: #4a4a4a;
    --paper: #ffffff;
    --backdrop: #eceae6;
  }
  * { box-sizing: border-box; margin: 0; padding: 0; }
  html, body { width: 1200px; height: 960px; overflow: hidden; }
  body {
    background: var(--backdrop);
    font-family: "Montserrat", sans-serif;
    display: flex; flex-direction: column; align-items: center; justify-content: center;
    gap: 32px;
  }
  .card {
    position: relative;
    width: 760px; height: 434px;
    overflow: hidden;
    box-shadow: 0 6px 18px rgba(0,0,0,.12);
  }
  /* Brand side */
  .card--brand { background: linear-gradient(135deg, var(--sky-deep), var(--sky)); color: var(--paper); }
  .brand-lockup {
    position: absolute; left: 0; right: 0; top: 170px;
    display: flex; align-items: center; justify-content: center; gap: 22px;
  }
  .brand-dot { width: 78px; height: 78px; border-radius: 50%; background: var(--paper); }
  .brand-name { font-size: 54px; font-weight: 400; letter-spacing: 1px; color: var(--paper); }
  .brand-url {
    position: absolute; left: 0; right: 0; bottom: 40px; text-align: center;
    font-size: 17px; letter-spacing: 2px; font-weight: 500;
  }
  /* Contact side */
  .card--contact { background: var(--paper); }
  .contact-lockup {
    position: absolute; right: 50px; top: 46px;
    display: flex; align-items: center; gap: 20px;
  }
  .contact-lockup .brand-dot { width: 68px; height: 68px; background: var(--sky); }
  .contact-lockup .brand-name { font-size: 38px; color: var(--ink); letter-spacing: .5px; }
  .person { position: absolute; left: 70px; top: 150px; }
  .person-name { font-size: 34px; font-weight: 800; color: var(--sky); letter-spacing: .5px; }
  .person-role, .person-quals { font-size: 15px; color: var(--grey); line-height: 1.5; }
  .person-role { margin-top: 4px; }
  .footer-band {
    position: absolute; left: 0; right: 0; bottom: 0; height: 152px;
    background: linear-gradient(180deg, var(--leaf) 0%, var(--steel) 30%, var(--sky) 60%, var(--sky-deep) 100%);
  }
  .contact-list {
    position: absolute; right: 34px; bottom: 22px;
    list-style: none; text-align: right; color: var(--paper);
  }
  .contact-list li {
    display: flex; align-items: center; justify-content: flex-end; gap: 14px;
    font-size: 19px; font-weight: 500; letter-spacing: 1px; line-height: 1.65;
  }
  .contact-list svg { width: 20px; height: 20px; flex: none; }
</style>
</head>
<body>
  <section class="card card--brand" aria-label="Brand side">
    <div class="brand-lockup">
      <span class="brand-dot"></span>
      <span class="brand-name">Thrive Lane</span>
    </div>
    <p class="brand-url">www.thrivelane.com</p>
  </section>

  <section class="card card--contact" aria-label="Contact side">
    <div class="contact-lockup">
      <span class="brand-dot"></span>
      <span class="brand-name">Thrive Lane</span>
    </div>
    <div class="person">
      <h1 class="person-name">Dara Whelby</h1>
      <p class="person-role">Counsellor &amp; Psychotherapist</p>
      <p class="person-quals">BSc (Psychol.), BA, Dip. (Couns. &amp; Psych.)<br>PG.Cert (CBT), FGTrK, ONRE</p>
    </div>
    <div class="footer-band" role="img" aria-label="Decorative green and blue wave band along the foot of the card"></div>
    <ul class="contact-list">
      <li>000 000 0000
        <svg viewBox="0 0 24 24" fill="none" stroke="#fff" stroke-width="2" stroke-linecap="round" stroke-linejoin="round"><path d="M5 3h4l2 5-2.5 1.5a11 11 0 0 0 6 6L16 13l5 2v4a2 2 0 0 1-2 2A16 16 0 0 1 3 5a2 2 0 0 1 2-2z"/></svg>
      </li>
      <li>dara@thrivelane.com
        <svg viewBox="0 0 24 24" fill="none" stroke="#fff" stroke-width="2" stroke-linejoin="round"><rect x="3" y="5" width="18" height="14"/><path d="M3 5l9 8 9-8"/></svg>
      </li>
      <li>www.thrivelane.com
        <svg viewBox="0 0 24 24" fill="none" stroke="#fff" stroke-width="1.8"><circle cx="12" cy="12" r="9"/><ellipse cx="12" cy="12" rx="4" ry="9"/><path d="M3 12h18M5 7h14M5 17h14"/></svg>
      </li>
    </ul>
  </section>
</body>
</html>
```